Personal training and nutrition business needs business card design

We need a business card that outlays our services and invites potential customers to join our team and take the first step to a healthier and more enjoyable life. We cater for any level of fitness and specialize in weight loss and conditioning, strength training, muscle gain and strength endurance. Whether you are just starting off or need some help getting to the next level of your journey we are here to get the job done.
We specialize in one on one or one on two personal training sessions and each program will be custom made to suit individual fitness goals of our clients

```html
<!DOCTYPE html>
<html lang="en">
<head>
<meta charset="utf-8">
<title>Stride &amp; Pulse – Business Card</title>
<link href="https://fonts.googleapis.com/css2?family=Roboto:wght@400;700;900&family=Oswald:wght@500&display=swap" rel="stylesheet">
<style>
  :root {
    --backdrop: #2c2c2c;
    --card: #1a1a1b;
    --card-front: #1c1c1d;
    --emboss: #3b3b3d;
    --purple: #6a3f9c;
    --purple-mid: #7b4aa8;
    --orchid: #a45aa8;
    --lilac: #a06ac0;
    --text-light: #e6e6e8;
    --white: #ffffff;
  }
  * { margin: 0; padding: 0; box-sizing: border-box; }
  html, body { width: 1200px; height: 1138px; overflow: hidden; }
  body {
    background: var(--backdrop);
    position: relative;
    font-family: "Roboto", Arial, sans-serif;
  }
  .card {
    position: absolute;
    width: 620px;
    height: 374px;
    border-radius: 12px;
    overflow: hidden;
  }
  .card-front { left: 274px; top: 186px; background: var(--card-front); }
  .card-back  { left: 276px; top: 608px; background: var(--card); }

  .front-brand {
    position: absolute;
    left: 0; right: 0; top: 150px;
    text-align: center;
    font-weight: 900;
    font-size: 52px;
    letter-spacing: 2px;
    color: var(--emboss);
  }
  .front-tagline {
    position: absolute;
    left: 0; right: 0; top: 334px;
    text-align: center;
    font-family: "Oswald", "Arial Narrow", sans-serif;
    font-weight: 500;
    font-size: 13px;
    letter-spacing: 1.3px;
    color: var(--orchid);
  }

  .back-brand {
    position: absolute;
    left: 26px; top: 50px;
    display: flex; align-items: center; gap: 18px;
  }
  .brand-square {
    width: 64px; height: 64px;
    border-radius: 8px;
    background: linear-gradient(135deg, var(--purple-mid), var(--orchid));
  }
  .brand-name {
    font-weight: 900;
    font-size: 38px;
    line-height: 1;
    color: var(--white);
    letter-spacing: 1px;
  }

  .person { position: absolute; left: 42px; top: 200px; }
  .person-name {
    font-weight: 900;
    font-style: italic;
    font-size: 23px;
    letter-spacing: 1px;
    color: var(--lilac);
  }
  .person-role { font-size: 16px; color: var(--text-light); margin-top: 4px; }

  .address {
    position: absolute; left: 42px; top: 282px;
    font-size: 16px; line-height: 24px; color: var(--text-light);
  }

  .contacts {
    position: absolute; left: 346px; top: 200px;
    list-style: none;
  }
  .contacts li {
    display: flex; align-items: center;
    height: 24px;
    font-size: 16px; color: var(--text-light);
  }
  .contacts svg { width: 14px; height: 14px; margin-right: 12px; fill: var(--purple-mid); }

  .band { position: absolute; left: 0; bottom: 0; width: 620px; height: 48px; }
  .band-text {
    position: absolute; right: 22px; bottom: 13px;
    font-size: 16px; color: var(--text-light);
  }
</style>
</head>
<body>
  <section class="card card-front">
    <div class="front-brand">STRIDE &amp; PULSE</div>
    <div class="front-tagline">PERSONAL TRAINING.&nbsp; NUTRITION. MOTIVATION</div>
  </section>

  <section class="card card-back">
    <div class="back-brand">
      <span class="brand-square"></span>
      <span class="brand-name">STRIDE &amp; PULSE</span>
    </div>

    <div class="person">
      <div class="person-name">MARCUS REED</div>
      <div class="person-role">Personal Trainer</div>
    </div>

    <div class="address">2814 Maple Ridge Lane<br>Austin Texas 78704</div>

    <ul class="contacts">
      <li><svg viewBox="0 0 16 16"><path d="M3 2h3l1.5 3.5-2 1.3a9 9 0 0 0 3.7 3.7l1.3-2L14 10v3a1 1 0 0 1-1 1A12 12 0 0 1 2 3a1 1 0 0 1 1-1z"/></svg>+1 (512) 555-0148</li>
      <li><svg viewBox="0 0 16 16"><path d="M1 3h14v10H1z M1 3l7 6 7-6" stroke="#1a1a1b" stroke-width="1.2"/></svg>marcus@strideandpulse.com</li>
      <li><svg viewBox="0 0 16 16"><circle cx="8" cy="8" r="7"/><path d="M1 8h14M8 1c-3 4-3 10 0 14M8 1c3 4 3 10 0 14" stroke="#1a1a1b" stroke-width="1" fill="none"/></svg>www.strideandpulse.com</li>
    </ul>

    <svg class="band" viewBox="0 0 620 48" preserveAspectRatio="none">
      <defs>
        <linearGradient id="bandLeft" x1="0" x2="1">
          <stop offset="0" stop-color="#a45aa8"/>
          <stop offset="1" stop-color="#7b4aa8"/>
        </linearGradient>
      </defs>
      <rect x="0" y="34" width="270" height="14" fill="url(#bandLeft)"/>
      <path d="M278 0H620V48H256Z" fill="#5e3a92"/>
    </svg>
    <div class="band-text">Personal Training | Nutrition | Motivation</div>
  </section>
</body>
</html>
```